Modern Business Card

Modern professional business card with more than just logo and demographic info. Something memorable.

We are a trendy/modern chiropractic group with an emphasis on neurology, hence the minimalist-type brain logo. We want to convey that modern and technical aspect with professionalism and the elite nature of our practice environment.

```html
<!DOCTYPE html>
<html lang="en">
<head>
<meta charset="utf-8">
<title>Northvale Chiropractic – Business Card</title>
<link rel="stylesheet" href="https://fonts.googleapis.com/css2?family=Open+Sans:wght@400;600;700&family=Tinos:wght@400&display=swap">
<style>
  :root {
    --backdrop: #e4e2df;
    --card: #2a2a2c;
    --card-deep: #1c1c1e;
    --card-mid: #333336;
    --card-light: #45454a;
    --accent: #3b78c8;
    --ink-light: #f1f1f1;
    --ink-soft: #d9d9d9;
  }
  * { margin: 0; padding: 0; box-sizing: border-box; }
  html, body {
    width: 1200px; height: 847px; overflow: hidden;
    background: var(--backdrop);
    font-family: "Open Sans", Arial, sans-serif;
  }
  .canvas {
    position: relative; width: 1200px; height: 847px;
    display: flex; align-items: center; justify-content: center; gap: 40px;
  }
  .card {
    position: relative; width: 540px; height: 309px;
    background: var(--card);
    box-shadow: 0 10px 28px rgba(0,0,0,.22);
    overflow: hidden;
  }
  .card-back__pattern {
    position: absolute; inset: 0;
    background:
      radial-gradient(circle at 66% 64%, rgba(59,120,200,.85) 0, rgba(59,120,200,.35) 30px, rgba(59,120,200,0) 60px),
      repeating-linear-gradient(135deg, rgba(255,255,255,0) 0 34px, rgba(255,255,255,.035) 34px 68px),
      linear-gradient(150deg, var(--card-deep) 0%, var(--card) 45%, var(--card-mid) 75%, var(--card-light) 100%);
  }
  .brand {
    position: absolute; left: 215px; top: 78px;
    display: flex; align-items: center; gap: 14px;
  }
  .brand__square { width: 46px; height: 46px; background: var(--accent); flex: none; }
  .brand__name {
    color: var(--ink-light); font-family: "Tinos", "Times New Roman", serif;
    font-weight: 400; text-transform: uppercase; line-height: 1;
  }
  .brand__line { display: block; }
  .brand__line--main { font-size: 38px; letter-spacing: 1px; }
  .brand__line--sub { font-size: 20px; letter-spacing: 2.4px; margin-top: 2px; }
  .person {
    position: absolute; right: 290px; top: 180px; text-align: right;
  }
  .person__name {
    color: var(--accent); font-weight: 600; font-size: 19px;
    letter-spacing: .5px; text-transform: uppercase; white-space: nowrap;
  }
  .person__role { color: var(--ink-soft); font-size: 15px; margin-top: 2px; }
  .divider {
    position: absolute; left: 266px; top: 178px;
    width: 1.5px; height: 70px; background: var(--accent);
  }
  .contact {
    position: absolute; left: 280px; top: 180px; list-style: none;
  }
  .contact__item {
    display: flex; align-items: center; gap: 7px;
    color: var(--ink-light); font-size: 14.5px; line-height: 22px; white-space: nowrap;
  }
  .contact__icon { width: 12px; height: 12px; flex: none; }
</style>
</head>
<body>
<main class="canvas">
  <section class="card card-back">
    <div class="card-back__pattern" role="img" aria-label="Tiled pattern of the practice's brand mark in dark greys, with one mark highlighted in blue"></div>
  </section>

  <section class="card card-front">
    <div class="brand">
      <span class="brand__square"></span>
      <div class="brand__name">
        <span class="brand__line brand__line--main">Northvale</span>
        <span class="brand__line brand__line--sub">Chiropractic</span>
      </div>
    </div>

    <div class="person">
      <p class="person__name">Darren Holloway</p>
      <p class="person__role">President</p>
    </div>

    <span class="divider"></span>

    <ul class="contact">
      <li class="contact__item">
        <svg class="contact__icon" viewBox="0 0 24 24" aria-hidden="true"><path fill="#3b78c8" d="M6.6 10.8a15.5 15.5 0 0 0 6.6 6.6l2.2-2.2c.3-.3.7-.4 1-.2 1.1.4 2.3.6 3.6.6.6 0 1 .4 1 1V20c0 .6-.4 1-1 1A17 17 0 0 1 3 4c0-.6.4-1 1-1h3.5c.6 0 1 .4 1 1 0 1.3.2 2.5.6 3.6.1.3 0 .7-.2 1z"/></svg>
        555-310-4872
      </li>
      <li class="contact__item">
        <svg class="contact__icon" viewBox="0 0 24 24" aria-hidden="true"><path fill="#3b78c8" d="M2 5h20v14H2z"/><path fill="none" stroke="#2a2a2c" stroke-width="2" d="M2 5l10 8 10-8"/></svg>
        darren@northvalechiro.com
      </li>
      <li class="contact__item">
        <svg class="contact__icon" viewBox="0 0 24 24" aria-hidden="true"><circle cx="12" cy="12" r="10" fill="#3b78c8"/><path fill="none" stroke="#2a2a2c" stroke-width="1.6" d="M2 12h20M12 2c3 3 3 17 0 20M12 2c-3 3-3 17 0 20"/></svg>
        www.northvalechiro.com
      </li>
    </ul>
  </section>
</main>
</body>
</html>
```